Wine label for family vineyard start-up

Brand new family vineyard needs a new label:

The information we need on the label is the following:
- Syrah & Nebbiolo (variety)
- Colle Verdanese (location)
- 2018 (vintage)

The style of the label should be graphic / minimal / masculine.

This is a wine made by three 35yr old guys

Target Market(s)

young & urban

Industry/Entity Type

Vineyard

Logo Text

Syrah & Nebbiolo / Colle Verdanese / 2018

Font styles to use
Sans Serif

Requirements
Must have
• clearly legible
• aesthetically pleasing [minimalist]
• sans serif

```html
<!DOCTYPE html>
<html lang="en">
<head>
<meta charset="utf-8">
<title>Colle Verdanese Syrah &amp; Nebbiolo 2018 – Label</title>
<link rel="stylesheet" href="https://fonts.googleapis.com/css2?family=Josefin+Sans:wght@300;400&display=swap">
<style>
  :root {
    --page: #ffffff;
    --label-field: #f3f3f3;
    --frame: #9a9a9a;
    --seal: #b3b3b3;
    --seal-text: #ffffff;
  }
  * { margin: 0; padding: 0; box-sizing: border-box; }
  html, body {
    width: 930px;
    height: 1200px;
    overflow: hidden;
    background: var(--page);
  }
  .canvas {
    position: relative;
    width: 930px;
    height: 1200px;
    background: var(--page);
  }
  .label {
    position: absolute;
    left: 230px;
    top: 247px;
    width: 470px;
    height: 705px;
    border: 2px solid var(--frame);
    background: var(--label-field);
  }
  .label__pattern {
    position: absolute;
    inset: 0;
    width: 100%;
    height: 100%;
    display: block;
  }
  .seal {
    position: absolute;
    left: 311px;
    top: 443px;
    width: 312px;
    height: 312px;
    border-radius: 50%;
    background: var(--seal);
    color: var(--seal-text);
    font-family: "Josefin Sans", sans-serif;
    text-align: center;
  }
  .seal__location,
  .seal__variety {
    position: absolute;
    left: 0;
    right: 0;
    font-size: 22px;
    font-weight: 300;
    letter-spacing: 0.13em;
    line-height: 1;
    white-space: nowrap;
  }
  .seal__location { top: 129px; }
  .seal__variety  { top: 161px; }
  .seal__vintage {
    position: absolute;
    left: 0;
    right: 0;
    top: 260px;
    font-size: 22px;
    font-weight: 300;
    letter-spacing: 0.22em;
    line-height: 1;
    padding-left: 0.22em;
  }
</style>
</head>
<body>
  <main class="canvas">
    <section class="label">
      <svg class="label__pattern" viewBox="0 0 470 705" preserveAspectRatio="none"
           role="img" aria-label="Fine grey line pattern of overlapping circles and vertical rules covering the label">
        <rect x="0" y="0" width="470" height="705" fill="var(--label-field)"/>
      </svg>
    </section>
    <div class="seal">
      <p class="seal__location">COLLE VERDANESE</p>
      <p class="seal__variety">SYRAH &amp; NEBBIOLO</p>
      <p class="seal__vintage">2018</p>
    </div>
  </main>
</body>
</html>
```